Web design for business website

I need a web design for a business website for one of our clients who is specialized in alarm management software. I would like you to design 3 web pages, one for each of the 3 pages. You need to process the corporate identity of our client to the web design. This means the colors of the logo (red and black) should definitely show up on all of the 3 pages. Find the logo file for the logo of our customer. To increase readability I suggest you use a white/light background. All suggestions are welcome.

Please kindly download atttached Webdesign.zip and read the project brief first. The project brief refers to all other files of the zip file. Your design must have exactly the same structure as the wireframes.
Updates

Target Market(s)

B2B, Alarm management

Industry/Entity Type

Business

Number of Pages Required

3 page

Requirements
Must have
• The web design must have exactly the same structure as the wireframes and needs to contain the colors of the company logo.

```html
<!DOCTYPE html>
<html lang="en">
<head>
<meta charset="utf-8">
<title>Korvant – Real-time reasoning solutions</title>
<link href="https://fonts.googleapis.com/css2?family=Open+Sans:wght@400;600;700;800&display=swap" rel="stylesheet">
<style>
:root{
  --navy:#1b1b30;
  --navy-2:#2a2b4a;
  --red:#c0391b;
  --ink:#222;
  --text:#555;
  --light:#f2f2f2;
  --band:#ececec;
  --footer:#232323;
  --footer-base:#1a1a1a;
}
*{box-sizing:border-box;margin:0;padding:0}
html,body{width:914px;height:1200px;overflow:hidden}
body{font-family:"Open Sans",Arial,sans-serif;background:#fff;position:relative;color:var(--text)}
.abs{position:absolute}

/* top bar */
.topbar{left:0;top:0;width:914px;height:37px;background:var(--navy);color:#ddd;font-size:11px}
.topbar .phone{left:83px;top:11px;display:flex;align-items:center;gap:5px}
.topbar .lang{left:594px;top:11px;display:flex;align-items:center;gap:5px}
.flag{width:11px;height:8px;background:linear-gradient(135deg,#238 0 35%,#fff 35% 45%,#c33 45% 55%,#fff 55% 65%,#238 65%)}
.search{left:668px;top:6px;width:163px;height:24px;background:var(--navy-2);border-radius:2px;font-size:10px;color:#aaa;padding:6px 10px}
.search svg{position:absolute;right:8px;top:6px}

/* header */
.header{left:0;top:37px;width:914px;height:97px;background:var(--light)}
.brand{left:82px;top:25px}
.brand-name{font-size:32px;font-weight:700;color:var(--navy);letter-spacing:.5px;line-height:34px}
.brand-tag{font-size:10.5px;color:var(--ink);margin-top:1px}
.hbtn{top:23px;width:47px;height:46px;background:#fff;border:1px solid #ddd;border-radius:2px;font-size:9px;color:#555;text-align:center;padding-top:8px}
.hbtn svg{display:block;margin:0 auto 3px}
.hbtn.account{color:var(--red)}

/* nav */
.nav{left:0;top:134px;width:914px;height:35px;background:linear-gradient(#d2431f,#b8311a)}
.nav a{position:absolute;top:11px;font-size:11px;color:#fff;text-decoration:none;transform:translateX(-50%);white-space:nowrap}
.nav .active{left:181px;top:3px;width:113px;height:32px;background:var(--light)}
.nav a.on{color:var(--red)}

/* hero */
.hero{left:0;top:169px;width:914px;height:338px;background:linear-gradient(180deg,#6f7680 0%,#c9a46a 30%,#f1b251 48%,#8b8266 62%,#4b5a3d 80%,#2f3b24 100%)}
.arrow{top:327px}
.dropdown{left:181px;top:168px;width:301px;height:128px;background:#efefef;box-shadow:0 2px 4px rgba(0,0,0,.15)}
.dropdown .thumb{position:absolute;left:14px;top:13px;width:100px;height:99px;background:linear-gradient(160deg,#1f3563,#3f6fa0 45%,#d8a23c 80%,#7a5a2a)}
.dropdown ul{position:absolute;left:129px;top:18px;list-style:none;font-size:10.5px;color:var(--ink)}
.dropdown li{height:26.5px;display:flex;gap:7px}
.dropdown li::before{content:"";width:3px;height:3px;background:var(--ink);margin-top:6px}
.dropdown li.on{color:var(--red)}
.dropdown li.on::before{background:var(--red)}

/* welcome */
.welcome h1{left:83px;top:540px;font-size:21px;font-weight:600;color:var(--red)}
.welcome p{left:83px;top:575px;width:518px;font-size:10.6px;line-height:17.2px;color:#555;hyphens:auto}
.welcome .photo{left:618px;top:546px;width:211px;height:161px;background:linear-gradient(180deg,#4f7fb8 0%,#7a9fc4 35%,#c9683a 65%,#3a3f56 100%)}
.rule{left:82px;top:736px;width:748px;height:1px;background:#ddd}

/* clients */
.clients h2{left:0;top:768px;width:914px;text-align:center;font-size:12.5px;font-weight:600;color:var(--ink)}
.client{top:808px;font-size:15px;font-weight:700;color:#444;display:flex;align-items:center;gap:6px;white-space:nowrap}
.client i{display:block;width:14px;height:14px;border-radius:50%;background:#888}

/* subscribe band */
.band{left:0;top:867px;width:914px;height:63px;background:var(--band)}
.social{top:886px;width:25px;height:25px;border-radius:50%}
.email{left:578px;top:884px;width:183px;height:29px;background:#fff;border-radius:2px;font-size:9.5px;color:#888;padding:8px 11px}
.subscribe{left:766px;top:884px;width:64px;height:29px;background:var(--navy);border-radius:2px;color:#fff;font-size:10.5px;text-align:center;line-height:29px}

/* footer */
.footer{left:0;top:930px;width:914px;height:188px;background:var(--footer)}
.fcol{top:958px;color:#bbb;font-size:9.5px}
.fcol h3{font-size:16px;font-weight:400;color:#fff;margin-bottom:9px}
.fcol ul{list-style:none}
.fcol li{height:18.7px;display:flex;gap:6px}
.fcol li::before{content:"";width:2px;height:2px;background:#999;margin-top:6px}
.fcol li.on{color:#fff}
.fcol li.on::before{background:#fff}
.vrule{left:616px;top:962px;width:1px;height:123px;background:#444}
.contact p{display:flex;gap:8px;margin-bottom:9px;line-height:16px;font-size:10px}
.contact svg{flex:none;margin-top:3px}

.base{left:0;top:1118px;width:914px;height:82px;background:var(--footer-base);color:#888;font-size:9.5px}
.base .copy{left:92px;top:24px}
.base .links{left:92px;top:47px;word-spacing:2px}
.circ{top:29px;width:26px;height:26px;border:2px solid #ddd;border-radius:50%}
.circ.up{border-color:#777}
.circ svg{position:absolute;left:5px;top:5px}
</style>
</head>
<body>

<div class="abs topbar">
  <div class="abs phone">
    <svg width="9" height="9" viewBox="0 0 10 10"><path d="M2 0l2 2.5-1 1.2c.6 1.3 1.6 2.3 2.9 2.9l1.2-1L10 8 8.6 10C4 9.7.3 6 0 1.4z" fill="#ddd"/></svg>
    Phone : +31 (0)20 555 0142
  </div>
  <div class="abs lang"><span class="flag"></span>English
    <svg width="7" height="4" viewBox="0 0 7 4"><path d="M0 0h7L3.5 4z" fill="#ddd"/></svg></div>
  <div class="abs search">Search
    <svg width="11" height="11" viewBox="0 0 12 12"><circle cx="5" cy="5" r="3.7" stroke="#ccc" stroke-width="1.8" fill="none"/><path d="M7.7 7.7L11 11" stroke="#ccc" stroke-width="2"/></svg></div>
</div>

<div class="abs header">
  <div class="abs brand">
    <div class="brand-name">Korvant</div>
    <div class="brand-tag">Real-time reasoning solutions</div>
  </div>
  <div class="abs hbtn account" style="left:674px">
    <svg width="12" height="13" viewBox="0 0 12 13"><circle cx="6" cy="3.5" r="3.3" fill="#c0391b"/><path d="M0 13c0-4 2.5-6 6-6s6 2 6 6z" fill="#c0391b"/></svg>Account</div>
  <div class="abs hbtn" style="left:729px">
    <svg width="11" height="13" viewBox="0 0 11 13"><path d="M2.5 6V3.5a3 3 0 016 0" stroke="#666" stroke-width="1.6" fill="none"/><rect y="6" width="11" height="7" rx="1" fill="#666"/></svg>Login</div>
  <div class="abs hbtn" style="left:784px">
    <svg width="13" height="13" viewBox="0 0 13 13"><rect x=".7" y="2" width="9.5" height="10" rx="1" stroke="#666" fill="none" stroke-width="1.3"/><path d="M5 8l1-2.5L11 .5l1.5 1.5-5 5z" fill="#666"/></svg>Signup</div>
</div>

<div class="abs nav">
  <div class="abs active"></div>
  <a style="left:127px">HOME</a>
  <a class="on" style="left:237px">INDUSTRY</a>
  <a style="left:353px">TELECOM</a>
  <a style="left:462px">POWER</a>
  <a style="left:570px">UTILITIES</a>
  <a style="left:674px">INFRA</a>
  <a style="left:771px">STORE</a>
</div>

<div class="abs hero" role="img" aria-label="Refinery silhouette at sunset beside a marsh"></div>
<svg class="abs arrow" style="left:16px" width="16" height="22" viewBox="0 0 16 22"><path d="M13 2L4 11l9 9" stroke="#1b1b30" stroke-width="4" fill="none"/></svg>
<svg class="abs arrow" style="left:881px" width="16" height="22" viewBox="0 0 16 22"><path d="M3 2l9 9-9 9" stroke="#1b1b30" stroke-width="4" fill="none"/></svg>

<div class="abs dropdown">
  <div class="thumb" role="img" aria-label="Industrial plant lit at night"></div>
  <ul>
    <li class="on">ALARM MANAGEMENT</li>
    <li>ASSET MANAGEMENT</li>
    <li>PREDICTIVE MAINTENANCE</li>
    <li>LOGIC DESIGN</li>
  </ul>
</div>

<section class="welcome">
  <h1 class="abs">WELCOME TO KORVANT</h1>
  <p class="abs">Companies have invested to get data out of processes. New technologies have been developed to get real-time data out of the harshest places, like oil-well drill heads or the Great Barrier Riff. Data in itself means nothing without the context the data is collected in. Example: data from equipment under maintenance does not provide information to operations. Information - data which is valid and meaningful - can overwhelm any user without the proper knowledge to interpret this information. Korvant technology enables easy applica&shy;tion of such knowledge in a comprehensible – visual – representation and makes hypothetical reasoning with information possible providing meaningful advisories to subscribers when they need it or when it is required that they are made aware of a situation which requires their attention.</p>
  <div class="abs photo" role="img" aria-label="Container port with cranes at dusk"></div>
</section>
<div class="abs rule"></div>

<section class="clients">
  <h2 class="abs">OUR CLIENTS</h2>
  <div class="abs client" style="left:84px"><i></i>Orvel</div>
  <div class="abs client" style="left:165px">Kestra</div>
  <div class="abs client" style="left:258px">Brouwmark</div>
  <div class="abs client" style="left:411px">Polymera</div>
  <div class="abs client" style="left:567px"><i></i>Nordhaven</div>
  <div class="abs client" style="left:700px">Qadira</div>
  <div class="abs client" style="left:770px">Conchia</div>
</section>

<div class="abs band"></div>
<div class="abs social" style="left:82px;background:#2a95d3"></div>
<div class="abs social" style="left:114px;background:#d8262d"></div>
<div class="abs social" style="left:145px;background:#1c6aa0"></div>
<div class="abs email">Email Address</div>
<div class="abs subscribe">Subscribe</div>

<footer class="abs footer"></footer>
<div class="abs fcol" style="left:80px">
  <h3>Solutions</h3>
  <ul><li class="on">AMX Alarm Reporting</li><li>AMX Alarm Analysis</li><li>AMX Alarm Expert</li><li>USE</li></ul>
</div>
<div class="abs fcol" style="left:239px">
  <h3>Industries</h3>
  <ul><li>Industry</li><li>Telecom</li><li>Power</li><li>Utilities</li><li>Infra</li></ul>
</div>
<div class="abs fcol" style="left:369px">
  <h3>About us</h3>
  <ul><li>Company</li><li>Overview</li><li>Leadership</li><li>Partners</li><li>Locations</li></ul>
</div>
<div class="abs fcol" style="left:494px">
  <h3>Industries</h3>
  <ul><li>Product News</li><li>Partner News</li><li>Events</li><li>Press Releases</li><li>Vacancies</li></ul>
</div>
<div class="abs vrule"></div>
<div class="abs fcol contact" style="left:665px">
  <h3>Contact us</h3>
  <p><svg width="9" height="10" viewBox="0 0 8 11"><path d="M4 0a4 4 0 014 4c0 3-4 7-4 7S0 7 0 4a4 4 0 014-4z" fill="#aaa"/><circle cx="4" cy="4" r="1.5" fill="#232323"/></svg><span>Address:<br>55 Building name, Street name<br>City - Zipcode</span></p>
  <p><svg width="9" height="9" viewBox="0 0 10 10"><path d="M2 0l2 2.5-1 1.2c.6 1.3 1.6 2.3 2.9 2.9l1.2-1L10 8 8.6 10C4 9.7.3 6 0 1.4z" fill="#aaa"/></svg>Phone: +31 (0)20 555 0142</p>
  <p><svg width="11" height="9" viewBox="0 0 11 8"><rect width="11" height="8" fill="#aaa"/><path d="M0 0l5.5 4.5L11 0" stroke="#232323" fill="none"/></svg>Email: info@korvant-mail.net</p>
</div>

<div class="abs base">
  <div class="abs copy">Copyright © 2015 KORVANT. All Rights Reserved.</div>
  <div class="abs links">Disclaimer | Support | Privacy Policy | Terms of use</div>
  <div class="abs circ" style="left:766px"><svg width="12" height="12" viewBox="0 0 12 12"><rect x="1" y="3" width="10" height="7" fill="#fff"/><path d="M1 3l5 4 5-4" stroke="#1a1a1a" fill="none"/></svg></div>
  <div class="abs circ up" style="left:797px"><svg width="12" height="12" viewBox="0 0 12 12"><path d="M6 11V2M2 6l4-4 4 4" stroke="#888" stroke-width="1.8" fill="none"/></svg></div>
</div>

</body>
</html>
```